Letterhead Design for Law Firm

**Edit: I have added the photo of a bottom that I like.

------
We are looking for a re-design of our new letterhead. The letterhead is for a law firm and will be used for digital and traditionally printed correspondence.

Here are some suggestions:

- Please use colours are #8ec900 and simple black.
- Please do not use any type of "waves" at the bottom of the page. This is not in style at all.
- Please stay modern yet conservative.
- Please use font Segoe UI Light or similar if you can
- Avoid clipart or illustrations.
- Utilize ample white space in the layout so the design looks clean and information is easy to read at a glance. Don't overcrowd the letterhead.
- Make sure the letterhead design is consistent with our brand identity (see corvelith.ca)
-Please, no black headers or footers.

I am attaching my current letterhead and signature for your convenience.

Remember, the letterhead is an extension of our professional identity. We are a successful firm and trial lawyers who correspond with insurers, judges, lawyers, courts, clients, etc. Make it new, modern, attractive, yet powerful and conservative.

It needs to be easily printable. I would like the bleed removed in print so the black bar the bottom crosses the page (but the text is not near the edges)
Updates

Low design quality

Target Market(s)

Clients, Government Offices, Judiciary, Lawyers, Insurance Companies, Colleagues.

Industry/Entity Type

Law

Other font styles liked:
• Segoe UI LIght, Calibri Light,

Colors
00AB8E
00BBA5
67D7C9
C6EFE9
E9F9F6

Requirements
Must have
• Everything that is on the letterhead now.
Nice to have
• Cutting Edge design, yet conservative.
Should not have
• law firm cliche design, images,

```html
<!DOCTYPE html>
<html lang="en">
<head>
<meta charset="utf-8">
<title>Marrow Personal Injury Lawyers — Letterhead</title>
<link rel="stylesheet" href="https://fonts.googleapis.com/css2?family=Roboto:wght@300;400;500;700&family=Roboto+Condensed:wght@400&display=swap">
<style>
  :root {
    --brand-green: #8ec900;
    --ink: #1a1a1a;
    --ink-soft: #333333;
    --grey-text: #555555;
    --body-text: #444444;
    --paper: #f6f4f5;
    --footer-black: #1b1b1b;
    --white: #ffffff;
  }
  * { margin: 0; padding: 0; box-sizing: border-box; }
  html, body { width: 935px; height: 1200px; overflow: hidden; background: var(--paper); }
  body { font-family: "Roboto", Arial, sans-serif; color: var(--ink); }
  .letterhead { position: relative; width: 935px; height: 1200px; background: var(--paper); }
  .abs { position: absolute; }

  .brand { left: 0; top: 100px; width: 935px; text-align: center; font-family: "Roboto", sans-serif; font-weight: 400; font-size: 28px; line-height: 34px; color: var(--ink); }

  .label-strong { font-weight: 500; font-size: 14px; color: var(--ink-soft); }
  .text-std { font-size: 15.5px; line-height: 20px; color: var(--ink-soft); }

  .file-info { right: 66px; top: 182px; text-align: right; color: var(--ink-soft); }
  .file-clerk { font-size: 15.5px; }
  .file-clerk strong { font-weight: 500; color: var(--ink); }
  .file-clerk span { color: var(--grey-text); }
  .file-email { font-size: 14px; margin-top: 4px; }
  .file-date { font-size: 14px; margin-top: 14px; }

  .re-label { left: 66px; top: 460px; color: var(--brand-green); font-weight: 700; font-size: 15px; }
  .re-block { left: 327px; top: 492px; }
  .divider { left: 62px; top: 574px; width: 807px; height: 1px; background: #444; }

  .body-copy { left: 69px; top: 606px; width: 796px; font-size: 11.4px; line-height: 17.6px; color: var(--body-text); text-align: justify; }
  .body-copy p + p { margin-top: 17px; }

  .closing { left: 69px; top: 838px; font-size: 14.5px; line-height: 19px; color: var(--ink-soft); }
  .signature { left: 67px; top: 890px; width: 256px; height: 56px; background: linear-gradient(90deg, rgba(0,0,0,0.08), rgba(0,0,0,0.02)); }
  .signatory { left: 69px; top: 962px; font-size: 14.5px; line-height: 17.7px; color: var(--ink-soft); }

  .contact { left: 69px; top: 1080px; font-size: 14px; line-height: 19px; color: var(--ink-soft); display: flex; align-items: center; }
  .contact-lines div { display: flex; align-items: center; gap: 5px; }
  .contact-sep { width: 2px; height: 28px; background: var(--brand-green); margin: 0 22px 0 18px; }

  .web-tab { left: 0; top: 1100px; }
  .web-url { right: 73px; top: 1113px; font-size: 16px; color: var(--ink); }

  .footer-bar { left: 0; top: 1142px; width: 935px; height: 58px; background: var(--footer-black); display: flex; align-items: center; justify-content: center; font-family: "Roboto Condensed", sans-serif; font-size: 17px; color: var(--white); gap: 8px; }
  .footer-bar .sep { color: var(--brand-green); }
</style>
</head>
<body>
<div class="letterhead">

  <header class="brand abs">Marrow Personal Injury Lawyers</header>

  <div class="abs label-strong" style="left:66px; top:182px;">Without Prejudice</div>
  <div class="abs label-strong" style="left:66px; top:230px;">By Email</div>

  <address class="abs text-std" style="left:65px; top:270px; font-style:normal;">
    Kestrel Mutual Insurance Company<br>
    Claims Litigation Department<br>
    240 Orchard Road South<br>
    P.O. Box 3100<br>
    Waterloo, ON &nbsp; N2J 0B7
  </address>

  <div class="abs text-std" style="left:65px; top:393px;">Attention:&nbsp; Mr. Dorian Pike</div>
  <div class="abs text-std" style="left:65px; top:420px;">Mr. Pike:</div>

  <div class="file-info abs">
    <div class="file-clerk"><strong>File Clerk:</strong> <span>Nadia Fairholm</span></div>
    <div class="file-email">nadia@corvelith.ca</div>
    <div class="file-date">March 13, 2024</div>
  </div>

  <div class="re-label abs">Re:</div>
  <div class="re-block abs text-std">
    Halvorsen v. Mercado et al.<br>
    DOL:&nbsp; September 12, 2019<br>
    Pre-Mediation Settlement Proposal – March 13th, 2024
  </div>

  <div class="divider abs"></div>

  <div class="body-copy abs">
    <p>Lorem ipsum dolor sit amet, consectetur adipiscing elit. Donec orci purus, luctus vitae dignissim eu, iaculis sed purus. Vivamus faucibus, ipsum nec aliquet viverra, leo mauris condimentum ligula, sit amet sagittis enim ligula quis arcu. Nam egestas tortor nisi porttitor mattis. In tortor ante, ultricies in suscipit a, tempus non massa. Vivamus et auctor mi. Fusce vel massa nulla. Phasellus nec eros mauris, et scelerisque orci.</p>
    <p>Donec malesuada orci vitae nulla accumsan porta a id massa. Quisque accumsan iaculis magna sit amet fringilla. Maecenas consequat, magna eget tincidunt semper, odio nibh rutrum mi, id feugiat ante nisi eu risus. Vestibulum nunc orci, rhoncus a placerat in, ultricies in mi. Cras mattis varius eros, vel fringilla nisi suscipit eget. Quisque scelerisque sagittis nulla at porttitor.</p>
    <p>Sed id augue vitae urna euismod commodo aliquet a quam. Pellentesque arcu velit, cursus et malesuada ut, consequat et diam. Nullam erat sem, rhoncus id ullamcorper vitae, rhoncus et arcu. In arcu adipiscing lacus, ac bibendum nulla leo eu purus. Quisque nec diam sed risus con-</p>
  </div>

  <div class="closing abs">
    Yours very truly,<br>
    MARROW PERSONAL INJURY LAWYERS
  </div>

  <div class="signature abs" role="img" aria-label="Handwritten signature of Owen T. Marrow"></div>

  <div class="signatory abs">
    Owen T. Marrow<br>
    Marrow Law Professional Corporation<br>
    /nf<br>
    Encl.
  </div>

  <div class="contact abs">
    <div class="contact-lines">
      <div>
        <svg width="13" height="13" viewBox="0 0 24 24" aria-hidden="true"><path fill="var(--brand-green)" d="M6.6 10.8a15.1 15.1 0 0 0 6.6 6.6l2.2-2.2c.3-.3.7-.4 1-.2 1.1.4 2.3.6 3.6.6.6 0 1 .4 1 1V20c0 .6-.4 1-1 1C10.6 21 3 13.4 3 4c0-.6.4-1 1-1h3.5c.6 0 1 .4 1 1 0 1.3.2 2.5.6 3.6.1.3 0 .7-.2 1z"/></svg>
        905-555-0142
      </div>
      <div>
        <svg width="13" height="13" viewBox="0 0 24 24" aria-hidden="true"><path fill="var(--brand-green)" d="M6 3h12v5H6zM3 9h18v8h-3v4H6v-4H3zm5 6v4h8v-4z"/></svg>
        905-555-0177
      </div>
    </div>
    <div class="contact-sep"></div>
    <div>
      88 Harbour Street W., Suite 1200<br>
      Hamilton, ON&nbsp; L8P 0A1
    </div>
  </div>

  <svg class="web-tab abs" width="935" height="42" viewBox="0 0 935 42" aria-hidden="true">
    <polygon points="626,37 656,8 935,8 935,37" fill="var(--brand-green)"/>
    <rect x="0" y="36" width="935" height="5" fill="var(--brand-green)"/>
  </svg>
  <div class="web-url abs">www.corvelith.cz</div>

  <footer class="footer-bar abs">
    <span>Long-Term Disability</span><span class="sep">|</span>
    <span>Serious Personal Injury</span><span class="sep">|</span>
    <span>Child &amp; Pediatric Injury Wrongful Death</span><span class="sep">|</span>
    <span>Employee Terminations</span>
  </footer>

</div>
</body>
</html>
```